A new presentation to our clients

we are a Real Estate agency, our website is www.lumibrasa.com and it’s time to have a new, fashion and remarcable Business Card. we want to differentiate ourselves from other companies so we want a business card that differentiates us. we want the business card to impact our customers. in the competitive market that we have today, we have to be different and it is this difference that we seek

Target Market(s)

Real Estate Clients

Contact Information for Business Card

We search a totaly diferent card from the usual

Font styles to use
Sans Serif

Colors
e34197

Requirements
Must have
• Logo, adress, phone contact, e-mail, photo, and our website
Nice to have
• We would like to see a modern business card
Should not have
• Houses or building draws

```html
<!DOCTYPE html>
<html lang="pt">
<head>
<meta charset="utf-8">
<title>Lumi Brasa — Business Card</title>
<link rel="stylesheet" href="https://fonts.googleapis.com/css2?family=Montserrat:wght@400;500;600;700&display=swap">
<style>
  :root {
    --brand-pink: #e8237a;
    --brand-pink-light: #f7277f;
    --ink: #1d1d1f;
    --paper: #ffffff;
    --backdrop: #18181a;
  }
  * { box-sizing: border-box; margin: 0; padding: 0; }
  html, body {
    width: 1200px; height: 900px; overflow: hidden;
    background: var(--backdrop);
    font-family: "Montserrat", sans-serif;
  }
  .stage {
    width: 1200px; height: 900px;
    display: flex; align-items: center; justify-content: center; gap: 44px;
  }
  .card {
    width: 520px; height: 304px; position: relative; overflow: hidden;
  }
  /* Back of card */
  .card--back {
    background: linear-gradient(135deg, var(--brand-pink-light) 0%, var(--brand-pink) 100%);
    display: flex; align-items: center; justify-content: center;
  }
  .brand-name {
    font-weight: 600; letter-spacing: 0.5px; white-space: nowrap;
  }
  .card--back .brand-name { color: var(--paper); font-size: 58px; }

  /* Front of card */
  .card--front { background: var(--paper); }
  .side-band {
    position: absolute; top: 10px; bottom: 10px; width: 24px;
    background: var(--brand-pink);
    display: flex; align-items: center; justify-content: center;
  }
  .side-band--left { left: 10px; }
  .side-band--right { right: 10px; }
  .band-text {
    writing-mode: vertical-rl; font-size: 11px; letter-spacing: 2.6px;
    text-transform: uppercase; white-space: nowrap;
  }
  .side-band--left .band-text { transform: rotate(180deg); color: var(--paper); }
  .side-band--right .band-text { color: var(--ink); font-weight: 500; }
  .band-text .accent { color: var(--paper); font-weight: 700; }

  .contact-row {
    position: absolute; top: 22px; left: 50px; right: 50px;
    display: flex; justify-content: space-between;
    font-size: 12px; text-transform: uppercase; color: var(--ink);
  }
  .person-name { font-weight: 600; letter-spacing: 0.4px; }
  .person-name .surname { color: var(--brand-pink); font-weight: 700; }
  .person-role { font-weight: 500; letter-spacing: 0.4px; }
  .person-role .divider { color: var(--brand-pink); margin: 0 4px; }

  .card--front .brand-name {
    position: absolute; left: 0; right: 0; top: 108px; text-align: center;
    color: var(--brand-pink); font-size: 50px;
  }
  .address {
    position: absolute; bottom: 22px; left: 50px; right: 50px;
    font-size: 11.5px; color: var(--ink); font-weight: 500;
  }
</style>
</head>
<body>
  <main class="stage">
    <section class="card card--back" aria-label="Business card back">
      <span class="brand-name">Lumi Brasa</span>
    </section>

    <section class="card card--front" aria-label="Business card front">
      <aside class="side-band side-band--left">
        <span class="band-text">geral@lumibrasa.com</span>
      </aside>
      <aside class="side-band side-band--right">
        <span class="band-text">www.lumi<span class="accent">brasa</span>.com</span>
      </aside>

      <header class="contact-row">
        <span class="person-name">Ricardo <span class="surname">Almeida</span></span>
        <span class="person-role">Director<span class="divider">|</span>(+351) 224 518 306</span>
      </header>

      <span class="brand-name">Lumi Brasa</span>

      <p class="address">Rua das Flores Novas, 148, 4050-262, Porto</p>
    </section>
  </main>
</body>
</html>
```